VELLUNDORA extra virgin olive oil label

We need a label design for a new range of products dedicated to the kitchen professionals. Ideally the label will be rectangular with a H10cm L15cm
The label needs to include the following:
Vellundora Logo
Olio Extravergine d'Oliva
1lt
Nutritional panel (see attached file)
Best before
Lot code
Product of Italy
Superior Category olive oil obtained directly from olives by mechanical processes only
Imported in Australia by
Ingredients: extra virgin olive oil
Produced and bottled by:
The final design should communicate quality, value and consistency to the kitchen professionals
The BESCA pasta sauce label can be a good example of the style we are after. see attached file

Target Market(s)

Kitchen professionals
The catch phrase is:
Bringing quality value and consistency to the kitchen professionals

This catch parse SHOULD NOT be included in the label

Industry/Entity Type

Kitchen

Font styles to use
Serif

Requirements
Must have
• Easy to read and easy to remember

```html
<!DOCTYPE html>
<html lang="it">
<head>
<meta charset="utf-8">
<title>Vellundora – Olio Extravergine d'Oliva label</title>
<link href="https://fonts.googleapis.com/css2?family=DM+Serif+Display&family=Libre+Baskerville:wght@400;700&display=swap" rel="stylesheet">
<style>
  :root {
    --page-bg: #ffffff;
    --label-cream: #f6f3e4;
    --ink-green: #1e3a22;
    --ink-dark: #2a2a22;
    --olive-light: #c3c84a;
    --olive-dark: #6f8a1e;
  }
  html, body {
    margin: 0;
    padding: 0;
    width: 689px;
    height: 1200px;
    overflow: hidden;
    background: var(--page-bg);
  }
  .canvas {
    position: relative;
    width: 689px;
    height: 1200px;
  }
  .label {
    position: absolute;
    left: 64px;
    top: 107px;
    width: 560px;
    height: 985px;
    overflow: hidden;
    background: var(--label-cream);
    color: var(--ink-dark);
    font-family: "Libre Baskerville", Georgia, serif;
  }
  .brand {
    position: absolute;
    top: 62px;
    left: 0;
    right: 0;
    display: flex;
    justify-content: center;
    align-items: center;
    gap: 10px;
  }
  .brand-mark {
    width: 12px;
    height: 12px;
    background: var(--ink-dark);
  }
  .brand-name {
    font-weight: 700;
    font-size: 28px;
    letter-spacing: 1px;
    color: var(--ink-dark);
  }
  .product-name {
    position: absolute;
    left: 50px;
    top: 222px;
    width: 190px;
    height: 570px;
    margin: 0;
    writing-mode: vertical-rl;
    transform: rotate(180deg);
    font-family: "DM Serif Display", Georgia, serif;
    font-weight: 400;
    font-size: 272px;
    line-height: 190px;
    text-align: center;
    color: var(--ink-green);
  }
  .descriptor {
    position: absolute;
    left: 288px;
    margin: 0;
    font-size: 21px;
    line-height: 31px;
    letter-spacing: 0.5px;
  }
  .descriptor.type { top: 252px; text-transform: uppercase; }
  .descriptor.category { top: 372px; }
  .descriptor.origin {
    top: 478px;
    font-size: 15px;
    line-height: 20px;
    text-transform: uppercase;
    letter-spacing: 1px;
  }
  .olive-art {
    position: absolute;
    left: 270px;
    top: 590px;
    width: 290px;
    height: 170px;
  }
  .volume {
    position: absolute;
    left: 270px;
    top: 926px;
    margin: 0;
    font-size: 16px;
    letter-spacing: 1px;
  }
</style>
</head>
<body>
<div class="canvas">
  <section class="label">
    <div class="brand">
      <span class="brand-mark"></span>
      <span class="brand-name">VELLUNDORA</span>
    </div>

    <h1 class="product-name">Olio</h1>

    <p class="descriptor type">Extravergine<br>D'Oliva</p>
    <p class="descriptor category">Superior Category<br>Olive Oil</p>
    <p class="descriptor origin">Product of Italy</p>

    <svg class="olive-art" viewBox="0 0 290 170" role="img" aria-label="Illustration of an olive sprig with two green olives and leaves">
      <defs>
        <radialGradient id="oliveTone" cx="45%" cy="55%" r="65%">
          <stop offset="0%" stop-color="var(--olive-light)"/>
          <stop offset="100%" stop-color="var(--olive-dark)"/>
        </radialGradient>
      </defs>
      <ellipse cx="150" cy="100" rx="135" ry="55" fill="url(#oliveTone)" opacity="0.55"/>
    </svg>

    <p class="volume">1LT</p>
  </section>
</div>
</body>
</html>
```